Website Design for a different kind of Business Consulting organisation needed!

We need a website design that reflects who we are, the simplicity of our consulting business and with a focus on our priority - to help our clients deliver, or execute - the "e" in Vantor-i.

Our key high level requirements are:
1) Simple and intuitive look and feel
2) Integration with all key social media platforms, twitter, facebook, linkedin, tumblr.

10 pages, tops.
- Main page - Welcome
- About Us/ Who are Vantor-i?
- 5 services pages - Project Management, Business Process Management, Change Management, Business Analysis and Finance Systems
- Contact Us

Something like:
http://www.lumvexhold.example/

Vantor-i is a registered trademark and all Logos and other branded material are attached for reference.

So, what’s our gig: A few snippets from previous work...

We are a different kind of business consulting group. We partner with our clients to help them deliver change. We don't just provide them with the theory. We also provide them with the leadership and capability to execute the change.

We aren’t a one stop shop, and we don’t offer cookie cutter solutions. We’re a boutique consulting firm covering Project Management, Business Process Management, Change Management and Business Analytics.

Vantor-i is a professional services organisation that partners with their clients to lead the execution of strategic process and system improvement initiatives. Vantor-i combines hands on delivery with coaching in best practice methodologies and approaches to build their clients capabilities to ensure their ongoing success in project implementations.

UPDATES:

Thanks to everyone who has submitted designs so far. The standard of designs coming through is quite high, with lots of professional designs that nail the design brief. Eliminating them is proving to be quite challenging.

A few updates to the job brief:
- Please make sure the design fits on one page. We would like all of our information to be on the first page that people see without them having to scroll down
- Please ensure you include the FIVE services we offer in the design
- Please use corporate images/istock photos in your designs which are relevant to our business
- Please add a section for a live twitter feed from our twitter account and a link to google+
- Please add a section for news/updates

Also, if you are able to build a site once a design is selected, please let us know.

Thanks,

Maribel.

Target Market(s)

Our target customers are large enterprises in Australia that are growing rapidly and have recently (last 24 months) undertaken or are currently undergoing software implementations and business process improvement programs. These businesses have a turnover of $100m or above and are working hard to differentiate themselves from their competitors but are not seeing the return on investment promised by software vendors and process improvement initiatives.

Industry/Entity Type

Leadership

Requirements
Must have
• Collaboration / Training / Workshop / Consulting images all of a professional nature.
Simple, non-cluttered look with plenty of white space.

```html
<!DOCTYPE html>
<html lang="en">
<head>
<meta charset="utf-8">
<title>Vantor-i – Change Management</title>
<link href="https://fonts.googleapis.com/css2?family=Open+Sans:wght@400;600;700&family=Lato:wght@400;700&display=swap" rel="stylesheet">
<style>
  :root{
    --brand:#0a55a5;
    --text:#555a5e;
    --heading:#3d4145;
    --nav:#8a8d90;
    --rule:#dcdcdc;
    --social:#6d7073;
    --white:#ffffff;
  }
  *{box-sizing:border-box;margin:0;padding:0}
  html,body{width:976px;height:1200px;overflow:hidden;background:var(--white)}
  body{position:relative;font-family:"Open Sans",Arial,sans-serif;color:var(--text)}
  .topbar{position:absolute;left:0;top:0;width:976px;height:6px;background:var(--brand)}
  .brand{position:absolute;left:98px;top:20px}
  .brand-name{font-family:"Open Sans",Arial,sans-serif;font-weight:400;font-size:42px;line-height:1;color:var(--brand);letter-spacing:1px}
  .brand-sub{position:absolute;left:113px;top:64px;font-size:8px;color:var(--brand);letter-spacing:.5px}
  .social-top{position:absolute;top:14px;left:749px;display:flex;gap:8px}
  .social-top span{width:26px;height:26px;border-radius:50%;background:var(--social)}
  .social-top span.active{background:var(--brand)}
  .main-nav{position:absolute;top:59px;left:0;width:976px;height:18px;font-family:"Lato",Arial,sans-serif;font-size:12.5px}
  .main-nav a{position:absolute;top:0;height:18px;line-height:18px;color:var(--nav);text-decoration:none}
  .main-nav a.current{background:var(--brand);color:var(--white);font-weight:700;text-align:center;width:86px}
  .rule{position:absolute;left:98px;width:780px;height:1px;background:var(--rule)}
  p{font-size:13px;line-height:20.3px}
  h1,h2{color:var(--brand);font-weight:600}
  .intro-icon{position:absolute;left:97px;top:123px;width:82px;height:82px}
  .intro{position:absolute;left:205px;top:122px;width:675px}
  .intro h1{font-size:22px;line-height:28px;margin-bottom:5px}
  .intro p+p{margin-top:7px}
  .photo{display:block}
  .photo-meeting{position:absolute;left:98px;top:346px;width:322px;height:278px;background:linear-gradient(135deg,#b9c3cc 0%,#e6ebf0 45%,#9aa7b6 100%)}
  .feature{position:absolute;left:465px;top:340px;width:420px}
  .feature h2{font-size:21px;line-height:27px;margin-bottom:5px}
  .feature h3{font-size:14.6px;font-weight:600;color:var(--heading);margin-top:18px;margin-bottom:2px}
  .checklist{list-style:none}
  .checklist li{position:relative;padding-left:29px;font-size:13px;line-height:24.4px}
  .checklist svg{position:absolute;left:4px;top:5px}
  .feature .closing{margin-top:16px;padding-left:3px}
  .story{position:absolute;left:106px;top:676px;width:778px}
  .story h2{font-size:21px;line-height:27px;margin-bottom:3px}
  .story p{hyphens:auto}
  .story p+p{margin-top:20.3px}
  .story strong{color:var(--heading);font-weight:700}
  .photo-dinner{float:right;width:323px;height:278px;margin:6px 4px 6px 28px;background:linear-gradient(135deg,#4a3a2e 0%,#8a7462 40%,#e8e6e2 70%,#cfcac4 100%)}
  .footer{position:absolute;left:0;top:1106px;width:976px;height:94px;background:var(--brand);color:var(--white)}
  .footer h4{font-size:10.6px;font-weight:700;line-height:14px;letter-spacing:.2px}
  .footer .small{font-size:9.4px;line-height:15.5px}
  .foot-col{position:absolute;top:17px}
  .foot-social{display:flex;gap:7px;margin-top:6px}
  .foot-social span{width:26px;height:26px;border-radius:50%;background:var(--white)}
  .foot-links{display:grid;grid-template-columns:60px auto;font-size:9.4px;line-height:15.5px}
  .foot-brand{position:absolute;left:706px;top:14px}
  .foot-brand .brand-name{color:var(--white);font-size:32px}
  .copyright{position:absolute;left:707px;top:60px;font-size:9.4px}
</style>
</head>
<body>
  <div class="topbar"></div>

  <header>
    <div class="brand"><span class="brand-name">Vantor-i</span></div>
    <div class="brand-sub">Pty Ltd</div>
    <div class="social-top" aria-label="Social links"><span></span><span></span><span></span><span class="active"></span></div>
    <nav class="main-nav">
      <a href="#" style="left:468px">HOME</a>
      <a href="#" style="left:541px">ABOUT</a>
      <a href="#" class="current" style="left:601px">SERVICES</a>
      <a href="#" style="left:705px">PARTNERS</a>
      <a href="#" style="left:800px">CONTACT</a>
    </nav>
  </header>

  <div class="rule" style="top:94px"></div>

  <svg class="intro-icon" viewBox="0 0 82 82" aria-hidden="true">
    <circle cx="41" cy="41" r="41" fill="var(--brand)"/>
    <path d="M30 27 a14 14 0 0 1 22 4" fill="none" stroke="#fff" stroke-width="3"/>
    <path d="M49 27 l4 5 l2-6 z" fill="#fff"/>
    <path d="M52 55 a14 14 0 0 1 -22 -4" fill="none" stroke="#fff" stroke-width="3"/>
    <path d="M33 55 l-4 -5 l-2 6 z" fill="#fff"/>
    <circle cx="27" cy="33" r="4" fill="#fff"/><rect x="22" y="38" width="10" height="8" rx="2" fill="#fff"/>
    <circle cx="55" cy="47" r="4" fill="#fff"/><rect x="50" y="52" width="10" height="8" rx="2" fill="#fff"/>
  </svg>

  <section class="intro">
    <h1>Change Management</h1>
    <p>Sed ut perspiciatis unde omnis iste natus error sit voluptatem accusantium doloremque laudantium, totam rem aperiam, eaque ipsa quae ab illo inventore veritatis et quasi architecto beatae vitae dicta sunt explicabo. Nemo enim ipsam voluptatem quia voluptas sit aspernatur aut odit aut fug set med itom.</p>
    <p>Lorem ipsum dolor sit amet, consectetur adipisicing elit, sed do eiusmod tempor incididunt ut labore et dolore in voluptate velit esse cillum dolore eu fugiat nulla pariatur.</p>
  </section>

  <div class="rule" style="top:300px"></div>

  <div class="photo photo-meeting" role="img" aria-label="Photo of two business consultants in a meeting by an office window"></div>

  <section class="feature">
    <h2>Lorem Ipsum Text Header h4 25px/33px</h2>
    <p>Sed ut perspiciatis unde omnis iste natus error sit voluptatem asantium doloremque laudantium, totam rem aperiam, eaque ipsa quae cabo. Nemo enim ipsam voluptatem quia voluptas.</p>
    <h3>Sample List Option</h3>
    <ul class="checklist">
      <li><svg width="17" height="15" viewBox="0 0 17 15" aria-hidden="true"><path d="M1 8 l5 5 l10-12" fill="none" stroke="var(--brand)" stroke-width="3"/></svg>Sed ut perspiciatis unde omnis iste natus error</li>
      <li><svg width="17" height="15" viewBox="0 0 17 15" aria-hidden="true"><path d="M1 8 l5 5 l10-12" fill="none" stroke="var(--brand)" stroke-width="3"/></svg>Sit voluptatem accusantium doloremque laudantium</li>
      <li><svg width="17" height="15" viewBox="0 0 17 15" aria-hidden="true"><path d="M1 8 l5 5 l10-12" fill="none" stroke="var(--brand)" stroke-width="3"/></svg>veritatis et quasi architecto beatae vitae dicta sunt</li>
    </ul>
    <p class="closing">Nemo enim ipsam voluptatem quia voluptas sit asper atur aut odit aut fugit, sed quia consequuntur magni dolores eos qui ratione voluptatem sequi nesciunt. Neque porro quisquam est.</p>
  </section>

  <section class="story">
    <div class="photo photo-dinner" role="img" aria-label="Photo of two senior businessmen talking over dinner with wine"></div>
    <h2>This is h4 25px with 33px Leading</h2>
    <p>Sed ut perspiciatis unde omnis iste natus error sit voluptatem accusantium doloremque laudantium, totam rem aperiam, eaque ipsa quae ab illo inventore veritatis et quasi architecto beatae vitae dicta sunt explicabo. <strong>This is bold Nemo enim ipsam</strong> volupteius modi tempora incidunt ut labore et dolore magnam aliquam quaerat voluptatem. Ut enim ad minima veniam, quis nostrum exercitationem ullam corporis suscipit laboriosam?</p>
    <p>Nisi ut aliquid ex ea commodi consequatur qui dolorem ipsum quia dolor sit amet, consectetur, adipisci velit, sed quia non numquam eius modi tempora incidunt ut labore et dolore magnam aliquam quaerat voluptatem. Ut enim ad minima veniam, quis nostrum exercitationem ullam corporis suscipit laboriosam, nisi ut aliquid ex ea ut perspiciatis unde omnis iste natus error sit voluptatem accusantium doloremque laudantium, totam rem aperiam, eaque ipsa quae ab illo inventore veritatis et quasi architecto beatae vitae dicta sunt explicabo. <strong>This is bold Nemo enim ipsam</strong> volupteius modi tempora incidunt ut labore et dolore magnam aliquam quaerat voluptatem. Ut enim ad minima veniam, quis nostrum exercitationem ullam corporis suscipit laboriosam, nisi ut aliquid ex ea commodi consequatur?</p>
  </section>

  <footer class="footer">
    <div class="foot-col" style="left:98px">
      <h4>CONNECT WITH US</h4>
      <div class="small">on social media network</div>
      <div class="foot-social"><span></span><span></span><span></span><span></span></div>
    </div>
    <div class="foot-col" style="left:269px">
      <h4>PAGES</h4>
      <div class="foot-links">
        <span>Home</span><span>Term &amp; Conditions</span>
        <span>About</span><span>FAQ</span>
        <span>Services</span><span>Partners</span>
      </div>
    </div>
    <div class="foot-col" style="left:463px">
      <h4>CONTACT DETAILS</h4>
      <div class="small">p: +61 3 555 014 207 &nbsp;f: +61 3 5550 1938<br>Level 4, 18 Harbour Lane, Melbourne,<br>Australia, 3000</div>
    </div>
    <div class="foot-brand"><span class="brand-name">Vantor-i</span></div>
    <div class="copyright">Copyright © 2014 All Rights Reserved</div>
  </footer>
</body>
</html>
```